Trade Show Display Graphic Design Project

We are looking for a design of a trade show display and podium that is color coordinated with our logo and advertisements (attached).
We are a security consulting firm that provides 4 core services:
-Security Assessment and Planning
-Security Design and Engineering
-Managed Security Services
-Security Training
Our look should reflect a highly professional elite level of expertise.
BACKDROP
We are looking for a backdrop trade show display that is a spin off of the print advertisement we are doing in the trade show magazine (attached advertisement OVRA 2016 Ad.pdf). I am looking to emphasize our core services, possibly with an icon to represent each service and keep the "Identifying - Mitigating - Managing - The Threat" as part of the overall display as see in the print advertisement.
The side curved endcaps can be used to show the logo and name vertically but i will ask you to be creative in how you do the design.
The design should be sleek and simple.
PODIUM
The podium I see as our logo. possibly rearranged with the logo art on top and the text on bottom.
Attached are the technical design requirements for the backdrop and podium. Only follow the technical requirements of the documents. All artwork should be sent to me through the pixelbazaar website.
LINK TO IMAGE IN SUPPLIED PDF
https://www.filevaultly.net/s/0a9b6i5j19umr4h/Stockaro_42038944_XXL.jpg?dl=0
Target Market(s)
security directors and senior directors
Industry/Entity Type
Security
Other font styles liked:
- Match logo font
Requirements
Must have
- logo, core services

```html
<!DOCTYPE html>
<html lang="en">
<head>
<meta charset="UTF-8">
<title>Halvern Consulting – Podium Front</title>
<link href="https://fonts.googleapis.com/css2?family=Open+Sans:wght@600&display=swap" rel="stylesheet">
<style>
  :root {
    --bg-charcoal: #252525;
    --brand-blue: #3fa2d6;
    --text-white: #f7f7f7;
    --guide-red: #e0262a;
  }
  * { margin: 0; padding: 0; box-sizing: border-box; }
  html, body {
    width: 1200px;
    height: 721px;
    overflow: hidden;
    background: var(--bg-charcoal);
  }
  .podium-panel {
    position: relative;
    width: 1200px;
    height: 721px;
    background: var(--bg-charcoal);
    font-family: "Open Sans", Arial, sans-serif;
  }
  .base-band {
    position: absolute;
    left: 0;
    top: 670px;
    width: 1200px;
    height: 51px;
    background: var(--brand-blue);
  }
  .mark-dot {
    position: absolute;
    left: 547px;
    top: 135px;
    width: 104px;
    height: 104px;
    border-radius: 50%;
    background: var(--brand-blue);
  }
  .brand-name {
    position: absolute;
    left: 370px;
    width: 453px;
    top: 298px;
    text-align: center;
    color: var(--text-white);
    font-weight: 600;
  }
  .brand-name .word-main {
    display: block;
    font-size: 86px;
    line-height: 1;
    letter-spacing: -2px;
  }
  .brand-name .word-sub {
    display: block;
    margin-top: 6px;
    font-size: 19px;
    line-height: 1;
    letter-spacing: 21px;
    padding-left: 21px;
  }
  .trim-guides {
    position: absolute;
    inset: 0;
    pointer-events: none;
  }
</style>
</head>
<body>
  <main class="podium-panel">
    <div class="base-band"></div>

    <div class="mark-dot" aria-hidden="true"></div>
    <h1 class="brand-name">
      <span class="word-main">halvern</span>
      <span class="word-sub">CONSULTING</span>
    </h1>

    <svg class="trim-guides" width="1200" height="721" viewBox="0 0 1200 721" aria-hidden="true">
      <g stroke="var(--guide-red)" stroke-width="1.6" stroke-dasharray="5 4" fill="none">
        <line x1="0" y1="105" x2="1200" y2="105"/>
        <line x1="0" y1="606" x2="1200" y2="606"/>
        <line x1="370" y1="0" x2="370" y2="708"/>
        <line x1="823" y1="0" x2="823" y2="708"/>
      </g>
    </svg>
  </main>
</body>
</html>
```